Corvane Capital Business Cards

These are professional business cards that are for my family office.
Put fake emails and phone numbers as of now until I finalize those components. This family office controls my families investments, assets, and future. The cards should be professional.
..
.
.
.
I just uploaded another variation of a logo I would like to see as a business card to I am inbeteen which logo to use

Target Market(s)

business

Industry/Entity Type

business

Contact Information for Business Card

Professional, wealth related, finance related.

Requirements
Must have
• Logo

```html
<!DOCTYPE html>
<html lang="en">
<head>
<meta charset="UTF-8">
<title>Corvane Capital Business Cards</title>
<link href="https://fonts.googleapis.com/css2?family=Cinzel:wght@600&family=Montserrat:wght@400;700&display=swap" rel="stylesheet">
<style>
  :root {
    --backdrop: #2e2e30;
    --card-white: #ffffff;
    --ink-navy: #1b1f2b;
    --ink-body: #2a2d35;
    --silver-light: #b4b4b6;
    --silver-dark: #8e8e91;
  }
  * { margin: 0; padding: 0; box-sizing: border-box; }
  html, body { width: 1200px; height: 1059px; overflow: hidden; background: var(--backdrop); }
  .canvas { position: relative; width: 1200px; height: 1059px; background: var(--backdrop); }

  .card { position: absolute; border-radius: 20px; overflow: hidden; }
  .card-front { left: 256px; top: 100px; width: 688px; height: 393px; background: var(--card-white); }
  .card-back {
    left: 253px; top: 535px; width: 694px; height: 397px;
    background: linear-gradient(100deg, var(--silver-light) 0%, #a9a9ac 45%, var(--silver-dark) 100%);
  }

  .headline-name {
    position: absolute; left: 30px; top: 30px;
    font-family: "Cinzel", serif; font-weight: 600; font-size: 46px;
    color: var(--ink-navy); letter-spacing: 1px; line-height: 1;
  }

  .brand-block { position: absolute; left: 474px; top: 20px; width: 194px; text-align: center; }
  .brand-circle { display: block; margin: 0 auto 10px; }
  .brand-name {
    font-family: "Cinzel", serif; font-weight: 600; font-size: 21px;
    color: var(--ink-navy); line-height: 1; white-space: nowrap;
  }

  .name-bar { position: absolute; left: 0; top: 200px; width: 20px; height: 55px; background: var(--ink-navy); }
  .person-name {
    position: absolute; left: 30px; top: 196px;
    font-family: "Montserrat", sans-serif; font-weight: 700; font-size: 31px;
    color: var(--ink-navy); line-height: 1.1;
  }
  .person-role {
    position: absolute; left: 30px; top: 233px;
    font-family: "Montserrat", sans-serif; font-weight: 400; font-size: 18px; color: var(--ink-body);
  }
  .divider { position: absolute; left: 30px; top: 274px; width: 633px; height: 2px; background: var(--ink-navy); }

  .contact-list { position: absolute; left: 30px; top: 290px; list-style: none; }
  .contact-item {
    display: flex; align-items: center; height: 27px;
    font-family: "Montserrat", sans-serif; font-size: 18px; color: var(--ink-body);
  }
  .contact-item svg { width: 14px; height: 14px; margin-right: 9px; fill: var(--ink-navy); }

  .address {
    position: absolute; right: 25px; top: 322px; text-align: right;
    font-family: "Montserrat", sans-serif; font-size: 18px; line-height: 27px; color: var(--ink-body);
  }
</style>
</head>
<body>
<div class="canvas">
  <section class="card card-front">
    <div class="headline-name">Corvane Capital</div>

    <div class="brand-block">
      <svg class="brand-circle" width="112" height="112" viewBox="0 0 112 112" aria-hidden="true">
        <circle cx="56" cy="56" r="53" fill="none" stroke="var(--ink-navy)" stroke-width="3"/>
      </svg>
      <div class="brand-name">Corvane Capital</div>
    </div>

    <div class="name-bar"></div>
    <div class="person-name">DANIEL HART</div>
    <div class="person-role">Managing Director</div>
    <div class="divider"></div>

    <ul class="contact-list">
      <li class="contact-item">
        <svg viewBox="0 0 24 24" aria-hidden="true"><path d="M6.6 10.8a15.1 15.1 0 0 0 6.6 6.6l2.2-2.2c.3-.3.7-.4 1-.2 1.1.4 2.3.6 3.6.6.6 0 1 .4 1 1V20c0 .6-.4 1-1 1A17 17 0 0 1 3 4c0-.6.4-1 1-1h3.5c.6 0 1 .4 1 1 0 1.3.2 2.5.6 3.6.1.3 0 .7-.2 1z"/></svg>
        123 456 789
      </li>
      <li class="contact-item">
        <svg viewBox="0 0 24 24" aria-hidden="true"><path d="M2 5h20v2l-10 6L2 7zM2 9l10 6 10-6v10H2z"/></svg>
        info@yourgmail.com
      </li>
      <li class="contact-item">
        <svg viewBox="0 0 24 24" aria-hidden="true"><path d="M12 2a10 10 0 1 0 0 20 10 10 0 0 0 0-20zm-1 17.9A8 8 0 0 1 4.1 11H8c0 3 1 6 3 8.9zM11 9H4.3A8 8 0 0 1 11 4.1C9.6 5.6 8.8 7.2 8.5 9zm2 0V4.1A8 8 0 0 1 19.7 9zm0 2h6.9a8 8 0 0 1-6.9 8.9z"/></svg>
        www.yourwebsite.com
      </li>
    </ul>

    <div class="address">Your address, City<br>State, Zip 1234</div>
  </section>

  <section class="card card-back" role="img" aria-label="Silver card back with a repeating embossed monogram pattern"></section>
</div>
</body>
</html>
```